Verodex business card

Business card for sustainable investment company called "Verodex". Verodex is an exchange platform selling carbon credits between buyers and sellers. Carbon Credits are an environmental commodity for reducing global carbon emissions.

the card should obviously have our logo and the theme should be sustainability/environment mixed with a trading platform.

Contact Information for Business Card

Logo, Name, Title, Phone, Email

Colors
0054AA
0677BA
7BADD7
CADEEF
E8F1F8
0094D4
00A9DD
6FCCEA
C7EBF8
E9F6FB
00AB8E
00BBA5
67D7C9
C6EFE9
E9F9F6
59FF00
82FF00
B8FF75
E3FFCB
F4FFEA

```html
<!DOCTYPE html>
<html lang="en">
<head>
<meta charset="utf-8">
<title>Verodex Business Card</title>
<link rel="stylesheet" href="https://fonts.googleapis.com/css2?family=Montserrat:wght@400;500;700&display=swap">
<style>
  :root {
    --backdrop: #3a3a3a;
    --navy: #0c2a55;
    --navy-deep: #0a2450;
    --ink: #14284a;
    --white: #ffffff;
    --paper: #f6f7f9;
    --cyan: #2fd9ea;
    --blue: #2a7fef;
    --muted-line: rgba(255,255,255,0.35);
  }
  * { margin: 0; padding: 0; box-sizing: border-box; }
  html, body {
    width: 1200px; height: 1200px; overflow: hidden;
    background: var(--backdrop);
    font-family: "Montserrat", Arial, sans-serif;
  }
  .canvas {
    position: relative; width: 1200px; height: 1200px;
    background: radial-gradient(circle at 50% 45%, #4a4a4a 0%, #2e2e2e 100%);
  }
  .card {
    position: absolute; left: 220px; width: 760px; height: 434px;
    border-radius: 26px; overflow: hidden;
    box-shadow: 0 18px 40px rgba(0,0,0,0.45);
  }
  .card--front { top: 126px; background: var(--navy); }
  .card--back {
    top: 640px;
    background: linear-gradient(135deg, var(--navy-deep) 0%, #143563 55%, var(--navy-deep) 100%);
  }

  /* front */
  .front__top {
    position: absolute; left: 0; top: 0; width: 100%; height: 212px;
    background: linear-gradient(180deg, var(--white), var(--paper));
  }
  .front__stripe {
    position: absolute; left: 0; top: 212px; width: 100%; height: 7px;
    background: linear-gradient(90deg, var(--blue) 0%, var(--cyan) 50%, var(--blue) 100%);
  }
  .front__gap {
    position: absolute; left: 0; top: 219px; width: 100%; height: 5px; background: var(--white);
  }
  .brand {
    position: absolute; display: flex; align-items: center; gap: 22px;
  }
  .brand__mark {
    width: 62px; height: 62px; border-radius: 10px; background: var(--blue);
  }
  .brand__name {
    font-weight: 700; font-size: 64px; letter-spacing: 1px; line-height: 1;
  }
  .front__top .brand { left: 140px; top: 72px; }
  .front__top .brand__name { color: var(--ink); }

  .person {
    position: absolute; left: 70px; top: 300px;
    padding-left: 16px; border-left: 5px solid var(--blue);
  }
  .person__name { color: var(--cyan); font-weight: 500; font-size: 28px; letter-spacing: 0.5px; }
  .person__title { color: var(--white); font-weight: 400; font-size: 15px; letter-spacing: 1px; margin-top: 2px; }

  .divider {
    position: absolute; left: 350px; top: 262px; width: 1px; height: 130px;
    background: var(--muted-line); transform: rotate(-25deg);
  }
  .contacts {
    position: absolute; left: 430px; top: 272px; list-style: none;
  }
  .contacts li {
    display: flex; align-items: center; gap: 12px;
    color: var(--white); font-size: 17px; margin-bottom: 14px;
  }
  .contacts svg { width: 20px; height: 20px; flex: none; }

  /* back */
  .card--back .brand { left: 150px; top: 180px; }
  .card--back .brand__mark { width: 80px; height: 80px; border-radius: 12px; }
  .card--back .brand__name { color: var(--white); font-size: 72px; }
</style>
</head>
<body>
<main class="canvas">
  <section class="card card--front" aria-label="Business card front">
    <div class="front__top">
      <div class="brand">
        <span class="brand__mark"></span>
        <span class="brand__name">VERODEX</span>
      </div>
    </div>
    <div class="front__stripe"></div>
    <div class="front__gap"></div>

    <div class="person">
      <p class="person__name">FULL NAME</p>
      <p class="person__title">POSITION</p>
    </div>

    <div class="divider"></div>

    <ul class="contacts">
      <li>
        <svg viewBox="0 0 24 24" aria-hidden="true"><path fill="#2fb8ee" d="M6.6 10.8a15 15 0 0 0 6.6 6.6l2.2-2.2a1 1 0 0 1 1-.25 11.4 11.4 0 0 0 3.6.57 1 1 0 0 1 1 1V20a1 1 0 0 1-1 1A17 17 0 0 1 3 4a1 1 0 0 1 1-1h3.5a1 1 0 0 1 1 1c0 1.25.2 2.45.57 3.6a1 1 0 0 1-.25 1z"/></svg>
        (000) 000 0000
      </li>
      <li>
        <svg viewBox="0 0 24 24" aria-hidden="true"><rect x="2" y="5" width="20" height="14" rx="1.5" fill="#2a8ff0"/><path d="M2.5 6l9.5 7 9.5-7" fill="none" stroke="#ffffff" stroke-width="1.5"/></svg>
        email@company.com
      </li>
      <li>
        <svg viewBox="0 0 24 24" aria-hidden="true"><g fill="none" stroke="#2a8ff0" stroke-width="1.6"><circle cx="12" cy="12" r="9.5"/><ellipse cx="12" cy="12" rx="4.5" ry="9.5"/><path d="M2.5 12h19M4 7h16M4 17h16"/></g></svg>
        www.company.com
      </li>
    </ul>
  </section>

  <section class="card card--back" aria-label="Business card back">
    <div class="brand">
      <span class="brand__mark"></span>
      <span class="brand__name">VERODEX</span>
    </div>
  </section>
</main>
</body>
</html>
```